New Innovative Counselling and psychotherapy Service needs Business Card design

Keep it simple and professional. On one side, just company name and logo (perhaps in all blue) and maybe a tag line.

On other side (all white) my name and Qualifications in centre

Industry/Entity Type

Health And Wellness

Contact Information for Business Card

Dara Whelby
Counsellor & Psychotherapist
BSc (Psychol.), BA, Dip. (Couns. & Psych.), PG.Cert (CBT), FGTrK, ONRE

I will also require Mobile no, Email and web site address of which I'll pass on to final designer.

Font styles to use
Sans Serif

Requirements
Must have
• My Logo Only and please use the colours in logo that is in it.
Should not have
• Any other images

```html
<!DOCTYPE html>
<html lang="en">
<head>
<meta charset="utf-8">
<title>Kindred Lane – Business Card</title>
<link href="https://fonts.googleapis.com/css2?family=Open+Sans:wght@400;600;700&display=swap" rel="stylesheet">
<style>
  :root {
    --backdrop: #3b3b3b;
    --card: #232324;
    --card-edge: #2c2c2d;
    --brand-blue: #42b0ea;
    --brand-green: #8fd35a;
    --text-light: #f2f2f2;
    --text-muted: #d6d6d6;
    --emboss: #4a4a4c;
  }
  * { margin: 0; padding: 0; box-sizing: border-box; }
  html, body {
    width: 799px; height: 1200px; overflow: hidden;
    background: var(--backdrop);
    font-family: "Open Sans", Arial, sans-serif;
  }
  .canvas {
    width: 799px; height: 1200px;
    display: flex; flex-direction: column;
    align-items: center; justify-content: space-around;
    padding: 60px 0;
  }
  .card {
    position: relative;
    width: 640px; height: 380px;
    border-radius: 26px;
    background: var(--card);
    box-shadow: 0 0 0 1px var(--card-edge);
    overflow: hidden;
  }

  /* Front face */
  .card-front {
    display: flex; align-items: center; justify-content: center;
  }
  .front-brand {
    display: flex; align-items: center; gap: 18px;
  }
  .front-brand .dot {
    width: 34px; height: 34px; border-radius: 50%;
    background: var(--emboss);
  }
  .front-brand .brand-name {
    font-weight: 600; font-size: 46px; color: var(--emboss);
    letter-spacing: 0.5px;
  }

  /* Back face */
  .card-back .brand {
    position: absolute; left: 38px; top: 34px;
    display: flex; align-items: center; gap: 14px;
  }
  .card-back .brand .dot {
    width: 40px; height: 40px; border-radius: 50%;
    background: var(--brand-blue);
  }
  .card-back .brand-name {
    font-weight: 600; font-size: 40px; line-height: 1;
    color: var(--text-light);
  }
  .details {
    position: absolute; left: 38px; top: 118px; width: 320px;
  }
  .person-name {
    font-weight: 700; font-size: 24px; color: var(--brand-blue);
    margin-bottom: 4px;
  }
  .role, .qualifications {
    font-size: 13.5px; line-height: 1.4; color: var(--text-muted);
  }
  .contact {
    list-style: none; margin-top: 16px;
  }
  .contact li {
    display: flex; align-items: center; gap: 10px;
    font-size: 15px; line-height: 1.55; color: var(--text-light);
  }
  .contact svg { width: 14px; height: 14px; flex: none; }
  .accent-circle {
    position: absolute; right: -70px; bottom: -90px;
    width: 360px; height: 360px; border-radius: 50%;
    background: var(--brand-blue);
  }
</style>
</head>
<body>
<main class="canvas">

  <section class="card card-front" aria-label="Card front">
    <div class="front-brand">
      <span class="dot"></span>
      <span class="brand-name">Kindred Lane</span>
    </div>
  </section>

  <section class="card card-back" aria-label="Card back">
    <div class="brand">
      <span class="dot"></span>
      <span class="brand-name">Kindred Lane</span>
    </div>

    <div class="details">
      <h1 class="person-name">Dara Whelby</h1>
      <p class="role">Counsellor &amp; Psychotherapist</p>
      <p class="qualifications">BSc (Psychol.), BA, Dip. (Couns. &amp; Psych.), PG.Cert (CBT), FGTrK, ONRE</p>
      <ul class="contact">
        <li>
          <svg viewBox="0 0 14 14" aria-hidden="true"><path d="M3 1h2.5l1 3-1.5 1a7 7 0 0 0 4 4l1-1.5 3 1V11a2 2 0 0 1-2 2A11 11 0 0 1 1 3a2 2 0 0 1 2-2z" fill="var(--brand-blue)"/></svg>
          0871 555 0142
        </li>
        <li>
          <svg viewBox="0 0 14 14" aria-hidden="true"><rect x="1" y="3" width="12" height="8" rx="1" fill="var(--brand-green)"/><path d="M1.5 3.5 7 8l5.5-4.5" fill="none" stroke="var(--card)" stroke-width="1"/></svg>
          dara.w@KindredLane.com
        </li>
        <li>
          <svg viewBox="0 0 14 14" aria-hidden="true"><circle cx="7" cy="7" r="5.5" fill="none" stroke="var(--brand-blue)" stroke-width="1.3"/><path d="M1.5 7h11M7 1.5c-2.5 3-2.5 8 0 11M7 1.5c2.5 3 2.5 8 0 11" fill="none" stroke="var(--brand-blue)" stroke-width="1"/></svg>
          www.KindredLane.com
        </li>
      </ul>
    </div>

    <div class="accent-circle" aria-hidden="true"></div>
  </section>

</main>
</body>
</html>
```